Road Construction Company needs business cards

We would like a new business card designed for our business.

We're a road construction company based in Qld, Australia.

Can the business card please have the following information on it.

Name: Warren Halbeck
Position: General Manager
Phone: 0472 915 348
Email: Warren.halbeck@tovrin.com.au
Address: 87 Marrow Ave, Pendlebay, QLD, 4023
Website: www.tovrin.com.au

Visually we'd like the card to be professional and simple.

Attached is our logo.

Our website is www.tovrin.com.au

Target Market(s)

Men aged 25-60

Contact Information for Business Card

As listed in project description

Font styles to use
Serif

Requirements
Must have
• Large logo on back of card

```html
<!DOCTYPE html>
<html lang="en">
<head>
<meta charset="utf-8">
<title>Tovrin Business Card</title>
<link rel="stylesheet" href="https://fonts.googleapis.com/css2?family=Mulish:wght@400;700;800&display=swap">
<style>
  :root {
    --canvas-bg: #e6e6e4;
    --brand-blue: #0d4a98;
    --brand-blue-light: #1668b3;
    --card-white: #f3f3f3;
    --text-grey: #5c5c5c;
    --rule-blue: #1553a3;
  }
  * { margin: 0; padding: 0; box-sizing: border-box; }
  html, body {
    width: 1200px; height: 1200px; overflow: hidden;
    background: var(--canvas-bg);
    font-family: "Mulish", sans-serif;
  }
  .card {
    position: absolute;
    left: 234px;
    width: 731px;
    height: 417px;
  }
  .card-front { top: 160px; }
  .card-back {
    top: 632px;
    background: linear-gradient(110deg, #ebebeb 0%, var(--card-white) 100%);
  }
  .front-pattern {
    position: absolute; inset: 0;
    background: linear-gradient(115deg, var(--brand-blue) 0%, var(--brand-blue-light) 100%);
  }
  .front-wordmark {
    position: absolute;
    left: 331px; top: 262px;
    font-size: 44px; font-weight: 800;
    letter-spacing: 2px;
    color: #ffffff;
    line-height: 1;
  }
  .contact-name {
    position: absolute; left: 360px; top: 63px;
    font-size: 31px; font-weight: 700;
    color: var(--brand-blue);
    line-height: 1;
  }
  .contact-title {
    position: absolute; left: 361px; top: 102px;
    font-size: 19px; color: var(--text-grey);
    line-height: 1;
  }
  .title-rule {
    position: absolute; left: 360px; top: 140px;
    width: 302px; height: 2px;
    background: var(--rule-blue);
  }
  .address {
    position: absolute; left: 360px; top: 208px;
    font-size: 19px; line-height: 26px;
    color: var(--text-grey);
  }
  .contact-list {
    position: absolute; left: 360px; top: 278px;
    list-style: none;
  }
  .contact-list li {
    display: flex; align-items: center;
    height: 28px;
    font-size: 19px; color: var(--text-grey);
  }
  .contact-list svg { width: 16px; height: 16px; margin-right: 9px; fill: var(--brand-blue); }
  .back-wordmark {
    position: absolute; left: 63px; top: 314px;
    font-size: 38px; font-weight: 800;
    letter-spacing: 2px;
    color: var(--brand-blue);
    line-height: 1;
  }
</style>
</head>
<body>
  <section class="card card-front">
    <div class="front-pattern" role="img" aria-label="Repeating embossed upward chevron pattern in shades of blue"></div>
    <div class="front-wordmark">TOVRIN</div>
  </section>

  <section class="card card-back">
    <h1 class="contact-name">Warren Halbeck</h1>
    <p class="contact-title">General Manager</p>
    <div class="title-rule"></div>
    <p class="address">87 Marrow Ave, Pendlebay,<br>QLD, 4023</p>
    <ul class="contact-list">
      <li>
        <svg viewBox="0 0 24 24" aria-hidden="true"><path d="M6.6 10.8a15.2 15.2 0 0 0 6.6 6.6l2.2-2.2a1 1 0 0 1 1-.25 11.4 11.4 0 0 0 3.6.57 1 1 0 0 1 1 1V20a1 1 0 0 1-1 1A17 17 0 0 1 3 4a1 1 0 0 1 1-1h3.5a1 1 0 0 1 1 1c0 1.25.2 2.45.57 3.6a1 1 0 0 1-.25 1z"/></svg>
        0472 915 348
      </li>
      <li>
        <svg viewBox="0 0 24 24" aria-hidden="true"><path d="M2 5h20v14H2z M3 6l9 7 9-7" fill="var(--brand-blue)"/><path d="M3 6.5l9 6.5 9-6.5" fill="none" stroke="#f0f0f0" stroke-width="1.6"/></svg>
        Warren.halbeck@tovrin.com.au
      </li>
      <li>
        <svg viewBox="0 0 24 24" aria-hidden="true"><circle cx="12" cy="12" r="10"/><path d="M2 12h20M12 2c3 3 3 17 0 20M12 2c-3 3-3 17 0 20" fill="none" stroke="#f0f0f0" stroke-width="1.5"/></svg>
        www.tovrin.com.au
      </li>
    </ul>
    <div class="back-wordmark">TOVRIN</div>
  </section>
</body>
</html>
```